Brisk Fixwell business card

I need business card for my business, I think you have all my details.six months ago I design with you car wrap design. We would like to design both side of the card. On front of card we would like logo , Name and our contact details.
At the back we are looking to mentioned our services.
The name will be:
Faridoullan Mestor
Managing Director
Ph:07952338417
Email:info@brisk-fixwell.com
Web:www.brisk-fixwell.com
So we have our logo, you don’t need to change the logo.
Please see the attachment.
Thanks

Target Market(s)

Home improvement

Industry/Entity Type

Home Improvement

Contact Information for Business Card

Company name: Brisk Fixwell
Name: Faridoullan Mestor
Position: Director
Ph:07952338417
Web: www.brisk-fixwell.com
Add: 42 Corvale Road
Hounslow
TW3 9KD
SECOND PERSON
Nizamuddel mestor
Position: Handyman
Ph: 07812 564037
Email: info@brisk-fixwell.com
Add: 18 Brackwin Lane Road
Hounslow
TW6 2LB

```html
<!DOCTYPE html>
<html lang="en">
<head>
<meta charset="utf-8">
<title>Brisk Fixwell business card</title>
<link href="https://fonts.googleapis.com/css2?family=Arimo:wght@400;700&display=swap" rel="stylesheet">
<style>
  :root {
    --backdrop: #2a2523;
    --card: #1a1a1b;
    --blue: #2b3f92;
    --red: #e0202e;
    --grey: #a3a3a6;
    --rule: #8a8a8d;
  }
  * { margin: 0; padding: 0; box-sizing: border-box; }
  html, body { width: 1200px; height: 842px; overflow: hidden; }
  body {
    background: var(--backdrop);
    font-family: "Arimo", Arial, sans-serif;
    position: relative;
  }
  .card {
    position: absolute;
    top: 266px;
    width: 540px;
    height: 310px;
    background: var(--card);
    overflow: hidden;
    box-shadow: 0 10px 30px rgba(0,0,0,.45);
  }
  .card--contact { left: 40px; }
  .card--services { left: 620px; }

  /* contact side */
  .band { position: absolute; left: 0; width: 100%; background: var(--blue); }
  .band--top { top: 0; height: 12px; }
  .band--bottom { bottom: 4px; height: 12px; }
  .band-accent { position: absolute; left: 0; bottom: 0; width: 100%; height: 4px; background: var(--red); }
  .contact {
    position: absolute;
    left: 0; right: 0; top: 62px;
    text-align: center;
    color: var(--grey);
    text-transform: uppercase;
  }
  .contact__name { color: var(--blue); font-weight: 700; font-size: 19px; letter-spacing: .5px; }
  .contact__role { font-size: 13px; margin-top: 2px; }
  .contact__rule { width: 120px; height: 1px; background: var(--rule); margin: 10px auto; }
  .contact__line { font-size: 14px; line-height: 19px; }
  .contact__phone { font-size: 19px; line-height: 24px; }

  /* services side */
  .tab { position: absolute; width: 28px; background: var(--blue); }
  .tab--left { left: 0; top: 150px; height: 52px; border-right: 4px solid var(--red); }
  .tab--right { right: 0; top: 52px; height: 40px; border-left: 4px solid var(--red); }
  .brand {
    position: absolute;
    left: 170px; top: 96px;
    display: flex; align-items: center; gap: 12px;
  }
  .brand__mark { width: 26px; height: 26px; background: var(--blue); }
  .brand__name { color: var(--blue); font-weight: 700; font-size: 30px; letter-spacing: 1px; text-transform: uppercase; }
  .services {
    position: absolute;
    left: 86px; right: 30px; top: 196px;
    color: var(--grey);
    font-size: 13.5px;
    line-height: 22px;
  }
  .services .sep { color: var(--red); margin: 0 5px; }
</style>
</head>
<body>
  <section class="card card--contact">
    <div class="band band--top"></div>
    <div class="contact">
      <p class="contact__name">Faridoullan Mestor</p>
      <p class="contact__role">Director</p>
      <div class="contact__rule"></div>
      <p class="contact__line">42 Corvale Road</p>
      <p class="contact__line">Hounslow, TW3 9KD</p>
      <div class="contact__rule"></div>
      <p class="contact__phone">07952338417</p>
      <p class="contact__line">info@brisk-fixwell.com</p>
      <p class="contact__line">www.brisk-fixwell.com</p>
    </div>
    <div class="band band--bottom"></div>
    <div class="band-accent"></div>
  </section>

  <section class="card card--services">
    <div class="tab tab--left"></div>
    <div class="tab tab--right"></div>
    <div class="brand">
      <span class="brand__mark"></span>
      <span class="brand__name">Brisk Fixwell</span>
    </div>
    <div class="services">
      <p>Plumbing<span class="sep">|</span>Carpentry<span class="sep">|</span>Painting and Decorating<span class="sep">|</span>Decking</p>
      <p>Fence<span class="sep">|</span>Gutter<span class="sep">|</span>Flooring<span class="sep">|</span>Plastering<span class="sep">|</span>Tilling<span class="sep">|</span>Gardening</p>
    </div>
  </section>
</body>
</html>
```